Harbourline Electrical Solutions

On one side. LOGO (underneath:) Commercial Industrial Residential

- NAME & CONTACT DETAILS

Marcus T. Hollings
Project Manager

(Cell icon) (441) 555-0187
(Email icon) hlelectricalsolutions@mailvento.com
(Facebook & Instagram icons )@hlelectricalsolutions

Other side: LOGO - underneath ELECTRICAL CONSTRUCTION & MAINTENANCE . LED LIGHTING & AUTOMATION . LIFE SAFETY SYSTEMS (FIRE ALARM / SECURITY) . DATA & COMMUNICATION

```html
<!DOCTYPE html>
<html lang="en">
<head>
<meta charset="UTF-8">
<title>Harbourline Electrical Solutions – Business Card</title>
<link href="https://fonts.googleapis.com/css2?family=Montserrat:wght@400;500;600;700&display=swap" rel="stylesheet">
<style>
  :root{
    --teal:#0f5468;
    --teal-light:#17687f;
    --white:#ffffff;
    --ring:#4a4a4a;
    --paper:#e4e4e4;
  }
  *{margin:0;padding:0;box-sizing:border-box}
  html,body{width:1200px;height:930px;overflow:hidden}
  body{background:var(--paper);font-family:"Montserrat",sans-serif;position:relative}
  .card{position:absolute;width:700px;height:400px;border-radius:26px;overflow:hidden;
        background:linear-gradient(135deg,var(--teal-light),var(--teal));color:var(--white)}
  .card--back{left:60px;top:50px}
  .card--front{left:440px;top:480px}

  /* back */
  .brand{display:flex;align-items:center;gap:18px}
  .brand__mark{width:22px;height:22px;border-radius:50%;background:currentColor;flex:none}
  .brand__name{font-weight:600;text-transform:uppercase;letter-spacing:2px;line-height:1.15}
  .card--back .brand{position:absolute;left:90px;top:90px}
  .card--back .brand__name{font-size:34px}
  .services{position:absolute;left:110px;top:245px;list-style:none}
  .services li{font-size:17px;font-weight:600;text-transform:uppercase;letter-spacing:1.5px;line-height:1.55;position:relative;padding-left:22px}
  .services li::before{content:"";position:absolute;left:0;top:10px;width:7px;height:7px;border-radius:50%;background:var(--white)}

  /* front */
  .disc{position:absolute;border-radius:50%}
  .disc--ring{left:362px;top:-70px;width:500px;height:500px;background:var(--ring)}
  .disc--face{left:374px;top:-70px;width:500px;height:500px;background:var(--white)}
  .card--front .brand{position:absolute;left:428px;top:120px;color:var(--teal);gap:16px}
  .card--front .brand__name{font-size:21px}
  .tagline{position:absolute;left:428px;top:225px;color:var(--teal);font-weight:600;font-size:13.5px;letter-spacing:.3px;white-space:nowrap}
  .person{position:absolute;left:50px;top:60px}
  .person__name{font-size:23px;font-weight:700;text-transform:uppercase;letter-spacing:1px;white-space:nowrap}
  .person__role{font-size:16px;font-weight:400;margin-top:4px}
  .contact{position:absolute;left:50px;font-size:16px;display:flex;align-items:center;gap:10px;white-space:nowrap}
  .contact svg{width:18px;height:18px;flex:none}
  .contact--social{top:190px}
  .contact--phone{top:290px}
  .contact--mail{top:322px}
  .social-dot{width:16px;height:16px;background:var(--white);border-radius:3px;flex:none}
</style>
</head>
<body>

<section class="card card--back" aria-label="Card back">
  <div class="brand">
    <span class="brand__mark"></span>
    <span class="brand__name">Harbourline<br>Electrical<br>Solutions</span>
  </div>
  <ul class="services">
    <li>Data &amp; Communication</li>
    <li>LED Lighting &amp; Automation</li>
    <li>Electrical Construction &amp; Maintenance</li>
    <li>Life Safety Systems (Fire Alarm / Security)</li>
  </ul>
</section>

<section class="card card--front" aria-label="Card front">
  <div class="disc disc--ring"></div>
  <div class="disc disc--face"></div>

  <div class="brand">
    <span class="brand__mark"></span>
    <span class="brand__name">Harbourline<br>Electrical<br>Solutions</span>
  </div>
  <p class="tagline">Commercial Industrial Residential</p>

  <div class="person">
    <h1 class="person__name">Marcus T. Hollings</h1>
    <p class="person__role">Project Manager</p>
  </div>

  <p class="contact contact--social"><span class="social-dot"></span>@hlelectricalsolutions</p>
  <p class="contact contact--phone">
    <svg viewBox="0 0 24 24" fill="none" stroke="currentColor" stroke-width="2"><rect x="7" y="2" width="10" height="20" rx="2"/><line x1="11" y1="18" x2="13" y2="18"/></svg>
    (441) 555-0187
  </p>
  <p class="contact contact--mail">
    <svg viewBox="0 0 24 24" fill="none" stroke="currentColor" stroke-width="2"><rect x="3" y="5" width="18" height="14" rx="1"/><polyline points="3,6 12,13 21,6"/></svg>
    hlelectricalsolutions@mailvento.com
  </p>
</section>

</body>
</html>
```